Mobile app for checking bus arrival

I would like to make the UI much more beautiful and modern. The app is an app to check bus arrival in Singapore.
See here: https://apps.veltrano.com/store/apps/details?id=com.ridoka&hl=en

Based on the question from designers:

1. The first screen shows the favorite bus stop. Each item shows location / street, the top one is the location, second line is the street name. And the number is the bus stop code.

2. Please download the app and try bus stop code with 07589 or 10079, for example. It will bring you to the next screen.

3. The pencil allow you to select color theme, for the list item, and the header.

4. On the second screen, it will show up the list of bus route that available on that bus stop.

5. When you tap on one of them it will show you the 2 subsequent arrival time.

6. Each of the arrival time has the information of availability seats available, seats not available, no more space. (we can use green, yellow, red, respectively).

7. Each of the arrival time has the WAB indicator (Wheelchair availability). Show as icon is preferred.

7. KLT and VOPN are the bus provider in Singapore. 48 means the route /service no.

Requirements:
And check the attachment, see screen 3. I need to add information about the space availability, which has 3 state: seats available, seats not available, no more space. (we can use green, yellow, red, respectively).

Please advise how to show the information.

Target Market(s)

Students, age below 35

Industry/Entity Type

Trivex

Requirements
Must have
• The app currently has the capabilities to select color theme, checkout screen1. It's the button and the list item color.
Nice to have
• Please download the app to see all available colors, and make suggestion to have better color pallete.

```html
<!DOCTYPE html>
<html lang="en">
<head>
<meta charset="utf-8">
<title>Bus Stop Code</title>
<link href="https://fonts.googleapis.com/css2?family=Open+Sans:wght@400;600&display=swap" rel="stylesheet">
<style>
  :root {
    --stage: #4a4d55;
    --header-blue: #4f7ef2;
    --white: #ffffff;
    --stop-green: #4cc35a;
    --code-green: #6fc23a;
    --title-ink: #2f3136;
    --street-ink: #7b7e85;
    --divider: #e3e4e7;
    --banner-deep: #7a3a0c;
    --banner-mid: #c8660f;
    --banner-light: #e8952a;
  }
  * { box-sizing: border-box; margin: 0; padding: 0; }
  html, body { width: 1200px; height: 900px; overflow: hidden; }
  body {
    background: var(--stage);
    font-family: "Open Sans", sans-serif;
    display: flex; align-items: center; justify-content: center;
  }
  .app-screen {
    width: 480px; height: 852px;
    background: var(--white);
    position: relative;
    overflow: hidden;
    display: flex; flex-direction: column;
  }
  .app-header { background: var(--header-blue); color: var(--white); }
  .status-bar {
    height: 30px; display: flex; align-items: center; justify-content: space-between;
    padding: 0 10px; font-size: 14px; font-weight: 600;
  }
  .status-left, .status-right { display: flex; align-items: center; gap: 6px; width: 150px; }
  .status-right { justify-content: flex-end; }
  .signal { display: flex; gap: 2px; }
  .signal i { width: 7px; height: 7px; border-radius: 50%; border: 1px solid var(--white); }
  .signal i.on { background: var(--white); }
  .battery { width: 30px; height: 13px; border: 1px solid var(--white); border-radius: 3px; padding: 1px; position: relative; }
  .battery::after { content: ""; position: absolute; right: -4px; top: 3px; width: 2px; height: 5px; background: var(--white); }
  .battery span { display: block; width: 22%; height: 100%; background: var(--white); }
  .nav-bar {
    height: 66px; display: flex; align-items: center; justify-content: space-between; padding: 0 18px;
  }
  .nav-title { font-size: 21px; font-weight: 400; letter-spacing: .2px; }
  .stop-list { list-style: none; }
  .stop-item {
    height: 66px; display: flex; align-items: center; padding-left: 24px;
  }
  .stop-badge {
    width: 40px; height: 40px; border-radius: 50%; background: var(--stop-green);
    display: flex; align-items: center; justify-content: center; flex: none;
  }
  .stop-text {
    margin-left: 18px; flex: 1; height: 100%;
    border-bottom: 1px solid var(--divider);
    display: flex; flex-direction: column; justify-content: center; line-height: 1.12;
  }
  .stop-code { color: var(--code-green); font-size: 13px; }
  .stop-name { color: var(--title-ink); font-size: 19px; }
  .stop-street { color: var(--street-ink); font-size: 13px; }
  .ad-banner {
    position: absolute; left: 0; bottom: 0; width: 480px; height: 75px;
  }
  .ad-art {
    position: absolute; inset: 0;
    background: linear-gradient(90deg, var(--banner-deep) 0%, var(--banner-mid) 45%, var(--banner-light) 80%, var(--banner-mid) 100%);
  }
  .ad-label {
    position: absolute; left: 28px; top: 8px; color: var(--white);
    font-size: 22px; line-height: 1.05; font-weight: 600;
  }
  .ad-brand {
    position: absolute; right: 26px; top: 20px; display: flex; align-items: center; gap: 8px;
    color: var(--white); font-size: 22px; font-weight: 600;
  }
  .ad-brand .dot { width: 26px; height: 26px; border-radius: 50%; background: var(--white); }
  .ad-brand small { font-size: 10px; font-weight: 600; }
  .ad-info {
    position: absolute; left: 6px; bottom: 5px; width: 13px; height: 13px;
    border: 1px solid var(--white); border-radius: 50%; color: var(--white);
    font-size: 9px; line-height: 11px; text-align: center;
  }
</style>
</head>
<body>
<main class="app-screen">
  <header class="app-header">
    <div class="status-bar">
      <div class="status-left">
        <span class="signal"><i class="on"></i><i class="on"></i><i class="on"></i><i></i><i></i></span>
        <span>Kestrel</span>
        <svg width="15" height="11" viewBox="0 0 15 11" aria-hidden="true"><path d="M1 4a9 9 0 0 1 13 0M3.5 6.5a5.5 5.5 0 0 1 8 0M7.5 10l-2-1.8a3 3 0 0 1 4 0z" fill="none" stroke="#fff" stroke-width="1.5"/></svg>
      </div>
      <span>4:21 PM</span>
      <div class="status-right">
        <svg width="8" height="13" viewBox="0 0 8 13" aria-hidden="true"><path d="M1 3.5l6 6-3 2.5V1l3 2.5-6 6" fill="none" stroke="#fff" stroke-width="1.1"/></svg>
        <span>22%</span>
        <span class="battery"><span></span></span>
      </div>
    </div>
    <nav class="nav-bar">
      <svg width="24" height="18" viewBox="0 0 24 18" aria-label="Menu"><path d="M0 2h24M0 9h24M0 16h24" stroke="#fff" stroke-width="1.6"/></svg>
      <h1 class="nav-title">Bus Stop Code</h1>
      <svg width="22" height="22" viewBox="0 0 22 22" aria-label="Search"><circle cx="9" cy="9" r="6.5" fill="none" stroke="#fff" stroke-width="2"/><path d="M14 14l6 6" stroke="#fff" stroke-width="2.2" stroke-linecap="round"/></svg>
    </nav>
  </header>

  <ul class="stop-list">
    <li class="stop-item">
      <span class="stop-badge"><svg width="16" height="20" viewBox="0 0 16 20"><path d="M8 18.5S2 12 2 8a6 6 0 0 1 12 0c0 4-6 10.5-6 10.5z" fill="none" stroke="#fff" stroke-width="1.6"/><circle cx="8" cy="8" r="2" fill="none" stroke="#fff" stroke-width="1.6"/></svg></span>
      <div class="stop-text"><span class="stop-code">09022</span><span class="stop-name">Opp Orchard stn</span><span class="stop-street">orchard boulevard</span></div>
    </li>
    <li class="stop-item">
      <span class="stop-badge"><svg width="16" height="20" viewBox="0 0 16 20"><path d="M8 18.5S2 12 2 8a6 6 0 0 1 12 0c0 4-6 10.5-6 10.5z" fill="none" stroke="#fff" stroke-width="1.6"/><circle cx="8" cy="8" r="2" fill="none" stroke="#fff" stroke-width="1.6"/></svg></span>
      <div class="stop-text"><span class="stop-code">10079</span><span class="stop-name">Blk 201</span><span class="stop-street">jln bt merah</span></div>
    </li>
    <li class="stop-item">
      <span class="stop-badge"><svg width="16" height="20" viewBox="0 0 16 20"><path d="M8 18.5S2 12 2 8a6 6 0 0 1 12 0c0 4-6 10.5-6 10.5z" fill="none" stroke="#fff" stroke-width="1.6"/><circle cx="8" cy="8" r="2" fill="none" stroke="#fff" stroke-width="1.6"/></svg></span>
      <div class="stop-text"><span class="stop-code">18141</span><span class="stop-name">Aft anglo-chinese jc</span><span class="stop-street">north bouna vista rd</span></div>
    </li>
    <li class="stop-item">
      <span class="stop-badge"><svg width="16" height="20" viewBox="0 0 16 20"><path d="M8 18.5S2 12 2 8a6 6 0 0 1 12 0c0 4-6 10.5-6 10.5z" fill="none" stroke="#fff" stroke-width="1.6"/><circle cx="8" cy="8" r="2" fill="none" stroke="#fff" stroke-width="1.6"/></svg></span>
      <div class="stop-text"><span class="stop-code">66081</span><span class="stop-name">Opp s'pore po..</span><span class="stop-street">bladdell rd</span></div>
    </li>
    <li class="stop-item">
      <span class="stop-badge"><svg width="16" height="20" viewBox="0 0 16 20"><path d="M8 18.5S2 12 2 8a6 6 0 0 1 12 0c0 4-6 10.5-6 10.5z" fill="none" stroke="#fff" stroke-width="1.6"/><circle cx="8" cy="8" r="2" fill="none" stroke="#fff" stroke-width="1.6"/></svg></span>
      <div class="stop-text"><span class="stop-code">08031</span><span class="stop-name">Dhob...</span><span class="stop-street">penang rd</span></div>
    </li>
    <li class="stop-item">
      <span class="stop-badge"><svg width="16" height="20" viewBox="0 0 16 20"><path d="M8 18.5S2 12 2 8a6 6 0 0 1 12 0c0 4-6 10.5-6 10.5z" fill="none" stroke="#fff" stroke-width="1.6"/><circle cx="8" cy="8" r="2" fill="none" stroke="#fff" stroke-width="1.6"/></svg></span>
      <div class="stop-text"><span class="stop-code">08031</span><span class="stop-name">Opp Orchard stn</span><span class="stop-street">orchard boulevard</span></div>
    </li>
    <li class="stop-item">
      <span class="stop-badge"><svg width="16" height="20" viewBox="0 0 16 20"><path d="M8 18.5S2 12 2 8a6 6 0 0 1 12 0c0 4-6 10.5-6 10.5z" fill="none" stroke="#fff" stroke-width="1.6"/><circle cx="8" cy="8" r="2" fill="none" stroke="#fff" stroke-width="1.6"/></svg></span>
      <div class="stop-text"><span class="stop-code">08031</span><span class="stop-name">Aft anglo-chinese jc</span><span class="stop-street">north bouna vista rd</span></div>
    </li>
  </ul>

  <aside class="ad-banner">
    <div class="ad-art" role="img" aria-label="Warm orange and brown textured backdrop of the test ad banner"></div>
    <p class="ad-label">320x50<br>Test Banner</p>
    <div class="ad-brand"><span class="dot"></span><span>Adlume</span><small>by Trivex</small></div>
    <span class="ad-info">i</span>
  </aside>
</main>
</body>
</html>
```